larkforge website

commerce website to sell cookeries, brackets, mailboxes and to show off homes built. Modern Steel in design see marlo cycles web page to be like: https://www.marlocycles-demo.com/en/ sorry its bright nest hosting word press divi

must be able to add products to page

Target Market(s)

mainly western states of U.S.

Industry/Entity Type

Building Product

Coding

Coded - Design and coding required

Number of Pages Required

3 page

Font styles to use
Sans Serif

Colors

Designer to choose colors to be used in the design.

Requirements
Must have
• customers to be able to order products from page
• bright nest hosting word press divi

```html
<!DOCTYPE html>
<html lang="en">
<head>
<meta charset="utf-8">
<title>Larkforge</title>
<link href="https://fonts.googleapis.com/css2?family=Arimo:wght@400;700&display=swap" rel="stylesheet">
<style>
:root{
  --blue:#3f5f8f;
  --blue-light:#6b8fc4;
  --ink:#2b2b2b;
  --muted:#6f6f6f;
  --white:#ffffff;
  --footer:#0e1519;
  --black:#000000;
}
*{box-sizing:border-box;margin:0;padding:0}
html,body{width:1200px;height:2850px;overflow:hidden}
body{position:relative;font-family:"Arimo",Arial,sans-serif;color:var(--ink);background:var(--white)}
.abs{position:absolute}

/* hero */
.hero{left:0;top:0;width:1200px;height:534px;background:radial-gradient(ellipse at 75% 40%,#5b6466 0%,#2a3134 40%,#14191b 100%)}
.hero-photo{left:0;top:0;width:1200px;height:534px;background:linear-gradient(100deg,rgba(60,70,40,.55) 0%,rgba(20,25,28,.2) 35%,rgba(110,115,110,.25) 70%,rgba(10,12,14,.6) 100%)}
.brand{display:flex;align-items:center;gap:8px;color:var(--white);font-weight:700;font-size:20px;letter-spacing:.5px}
.brand-mark{width:14px;height:14px;background:var(--white)}
.site-brand{left:123px;top:28px}
.nav{top:38px;display:flex;font-size:14px;font-weight:700;color:var(--white);left:403px;gap:0}
.nav a{color:inherit;text-decoration:none;position:absolute;white-space:nowrap}
.nav a.active{color:var(--blue-light);border-bottom:2px solid var(--blue-light);padding-bottom:6px}
.cart{left:988px;top:30px;width:108px;height:33px;border:1px solid var(--blue-light);display:flex;align-items:center;justify-content:center;gap:12px;color:var(--white);font-size:11px;font-weight:700}
.hero-title{left:0;width:1170px;top:196px;text-align:center;font-size:42px;font-weight:700;color:var(--white)}
.hero-text{left:293px;top:263px;width:595px;font-size:17px;line-height:19px;color:var(--white);text-align:justify;text-align-last:center}
.btn{background:var(--blue);color:var(--white);display:flex;align-items:center;justify-content:center;font-size:20px}
.hero-btn{left:477px;top:382px;width:213px;height:53px}
.dot{width:10px;height:10px;border-radius:50%;background:var(--white);top:482px}
.dot.on{width:14px;height:14px;top:480px;background:var(--blue);border:3px solid var(--white)}

/* about */
.about-photo{left:140px;top:609px;width:503px;height:382px;background:radial-gradient(ellipse at 60% 30%,#d9d4d8 0%,#8c7d86 35%,#3b3039 70%,#1f1a1f 100%)}
.about-title{right:112px;top:632px;font-size:27px;font-weight:700}
.about-rule{left:948px;top:668px;width:140px;height:5px;background:var(--blue)}
.about-lead{right:112px;top:702px;width:430px;text-align:right;font-size:16px;line-height:19px}
.about-body{left:682px;top:768px;width:406px;font-size:13px;line-height:19px;color:var(--muted);text-align:justify;text-align-last:right}
.about-btn{left:874px;top:910px;width:213px;height:53px}

/* manufacture */
.manu{left:0;top:1089px;width:1200px;height:671px;background:radial-gradient(ellipse at 45% 40%,#6b4a2a 0%,#2e2a27 40%,#121618 100%)}
.card{background:var(--white);text-align:center}
.card h3{font-size:18px;font-weight:400;color:var(--ink)}
.card p{font-size:11px;line-height:15px;color:var(--muted);text-align:justify;text-align-last:center}
.prod-shot{background:linear-gradient(180deg,#e9e9e9,#cfcfcf);border-radius:4px}
.flame{left:420px;top:1161px;width:228px;height:286px;background:linear-gradient(160deg,#2a2420 0%,#c0601a 45%,#5a3720 70%,#1a1613 100%)}
.manu-box{left:420px;top:1447px;width:228px;height:193px;background:var(--blue);color:var(--white)}
.manu-box h2{font-size:29px;font-weight:700;position:absolute;left:4px;top:15px}
.manu-box p{position:absolute;left:12px;top:53px;width:200px;font-size:11px;line-height:15.5px;font-weight:700;text-align:justify}

/* products */
.products-title{left:111px;top:1804px;font-size:28px;font-weight:700}
.products-text{left:111px;top:1854px;font-size:13px;line-height:16px;color:var(--muted)}
.shop{left:159px;top:1930px;font-size:26px;color:var(--muted)}
.count{left:159px;top:1990px;font-size:13px;color:var(--muted)}
.sort{left:893px;top:1984px;width:177px;height:33px;border:1px solid #bbb;font-size:13px;color:var(--muted);display:flex;align-items:center;padding-left:9px;gap:4px}
.sale{width:40px;height:40px;border-radius:50%;background:var(--black);color:var(--white);font-size:12px;display:flex;align-items:center;justify-content:center;top:2042px}
.shot{top:2068px;width:210px;height:255px}
.item-name{top:2351px;font-size:13px;color:var(--muted)}
.price{top:2376px;font-size:11px}
.price s{color:var(--muted)}
.add{top:2402px;width:135px;height:31px;background:var(--black);color:var(--white);font-size:12px;display:flex;align-items:center;justify-content:center}
.arrow{top:2451px;width:29px;height:31px;background:var(--black);display:flex;align-items:center;justify-content:center}

/* footer */
.footer{left:0;top:2527px;width:1200px;height:323px;background:var(--footer);color:var(--white)}
.footer .brand{color:var(--blue-light)}
.footer .brand-mark{background:var(--blue-light)}
.f-line{font-size:16px;line-height:19px;display:flex;gap:10px}
.f-head{font-size:17px;color:var(--blue-light)}
.f-link{font-size:16px}
.copy{left:0;width:1106px;text-align:center;top:2830px;font-size:11px;color:var(--white)}
</style>
</head>
<body>

<header class="abs hero">
  <div class="abs hero-photo" role="img" aria-label="Photo of a hand lifting the lid of a kettle grill"></div>
  <div class="abs brand site-brand"><span class="brand-mark"></span>LARKFORGE</div>
  <nav class="abs nav" style="left:0;top:38px;width:1200px">
    <a class="active" style="left:403px">HOME</a>
    <a style="left:492px">ABOUT US</a>
    <a style="left:610px">PRODUCT</a>
    <a style="left:727px">MANUFACTURE</a>
    <a style="left:880px">CONTACTS</a>
  </nav>
  <div class="abs cart">
    <svg width="20" height="16" viewBox="0 0 20 16" fill="none" stroke="#fff" stroke-width="1.5"><path d="M1 1h3l2 9h10l2-7H5"/><circle cx="8" cy="14" r="1.3"/><circle cx="15" cy="14" r="1.3"/></svg>
    My Cart
  </div>
  <h1 class="abs hero-title">CONSECTETUR ADIPISCING</h1>
  <p class="abs hero-text">Lorem ipsum dolor sit amet, consectetur adipiscing elit, sed do eiusmod tempor incididunt ut labore et dolore magna aliqua. Quis ipsum suspendisse ultrices gravida. Risus commodo viverra maecenas accumsan lacus vel facilisis.</p>
  <div class="abs btn hero-btn">Our Services</div>
  <span class="abs dot" style="left:538px"></span>
  <span class="abs dot" style="left:557px"></span>
  <span class="abs dot on" style="left:575px"></span>
  <span class="abs dot" style="left:597px"></span>
</header>

<section>
  <div class="abs about-photo" role="img" aria-label="Photo of meat smoking on a charcoal grill"></div>
  <h2 class="abs about-title">ABOUT US</h2>
  <div class="abs about-rule"></div>
  <p class="abs about-lead">Lorem ipsum dolor sit amet, consectetur adipiscing elit, sed do eiusmod tempor incididunt</p>
  <p class="abs about-body">ut labore et ultrices gravida. Risus commodo viverra maecenas accumsan lacus dolore magna aliqua. Quis ipsum suspendisse ultrices ut labore et dolore magna aliqua. Quis ipsum suspendisse ultrices gravida. Risus commodo viverra maecenas accumsan lacus vel facilisis.</p>
  <div class="abs btn about-btn">Read More</div>
</section>

<section class="abs manu" role="img" aria-label="Background photo of food cooking over grill flames"></section>

<div class="abs card" style="left:112px;top:1161px;width:308px;height:479px">
  <div class="abs prod-shot" style="left:95px;top:15px;width:125px;height:118px" role="img" aria-label="Photo of assorted portable grills"></div>
  <h3 class="abs" style="left:0;width:308px;top:141px">Cooking Equipmebnts</h3>
  <p class="abs" style="left:38px;width:242px;top:165px">ut labore et ultrices gravida. Risus commodo viverra maecenas accumsan lacus dolore magna aliqua. Quis ipsum suspendis</p>
  <div class="abs prod-shot" style="left:92px;top:218px;width:112px;height:150px" role="img" aria-label="Photo of a kettle grill"></div>
  <h3 class="abs" style="left:0;width:286px;top:374px">Preparation Equipmebnts</h3>
  <p class="abs" style="left:28px;width:242px;top:406px">ut labore et ultrices gravida. Risus commodo viverra maecenas accumsan lacus dolore magna aliqua. Quis ipsum suspendis</p>
</div>

<div class="abs flame" role="img" aria-label="Photo of a spatula over a burger on a flaming grill"></div>
<div class="abs manu-box">
  <h2>MANUFACTURE</h2>
  <p>ut labore et ultrices gravida. Risus commodo viverra maecenas accumsan lacus dolore magna aliqua. Quis ipsum suspendis magna aliqua. Quis ipsum su</p>
</div>

<div class="abs card" style="left:649px;top:1212px;width:309px;height:235px">
  <div class="abs prod-shot" style="left:95px;top:10px;width:120px;height:138px" role="img" aria-label="Photo of a gas grill"></div>
  <h3 class="abs" style="left:0;width:313px;top:155px">Bar Equipmebnts</h3>
  <p class="abs" style="left:43px;width:242px;top:180px">ut labore et ultrices gravida. Risus commodo viverra maecenas accumsan lacus dolore magna aliqua. Quis ipsum suspendis</p>
</div>

<div class="abs card" style="left:649px;top:1447px;width:440px;height:193px">
  <div class="abs prod-shot" style="left:40px;top:14px;width:125px;height:165px" role="img" aria-label="Photo of a kettle grill on wheels"></div>
  <h3 class="abs" style="left:185px;width:230px;top:53px">Outdoor Equipmebnts</h3>
  <p class="abs" style="left:186px;width:242px;top:86px">ut labore et ultrices gravida. Risus commodo viverra maecenas accumsan lacus dolore magna aliqua. Quis ipsum suspendis</p>
</div>

<section>
  <h2 class="abs products-title">PRODUCTS</h2>
  <p class="abs products-text">Lorem ipsum dolor sit amet, consectetur adipiscing elit, sed do eiusmod tempor incididunt ut labore et dolore magna aliqua.<br>Quis ipsum suspendisse ultrices gravida. Risus commodo viverra maecenas accumsan lacus vel facilisis.</p>
  <div class="abs shop">Shop</div>
  <div class="abs count">showing 1-30 of 32 results</div>
  <div class="abs sort">Sort by price: high to low
    <svg width="8" height="6" viewBox="0 0 8 6"><path d="M1 1l3 3 3-3" stroke="#555" fill="none" stroke-width="1.4"/></svg>
  </div>

  <div class="abs sale" style="left:418px">sale!</div>
  <div class="abs sale" style="left:725px">sale!</div>
  <div class="abs sale" style="left:1033px">sale!</div>

  <div class="abs shot prod-shot" style="left:157px" role="img" aria-label="Product photo of a kettle grill"></div>
  <div class="abs shot prod-shot" style="left:465px" role="img" aria-label="Product photo of a gas grill"></div>
  <div class="abs shot prod-shot" style="left:772px" role="img" aria-label="Product photo of a bucket grill"></div>

  <div class="abs item-name" style="left:164px">Master Package Outdoor</div>
  <div class="abs item-name" style="left:471px">Master Package Outdoor</div>
  <div class="abs item-name" style="left:778px">Master Package Outdoor</div>

  <div class="abs price" style="left:159px"><s>$ 1,457.00</s> $999.00</div>
  <div class="abs price" style="left:467px"><s>$ 1,457.00</s> $999.00</div>
  <div class="abs price" style="left:774px"><s>$ 1,457.00</s> $999.00</div>

  <div class="abs add" style="left:161px">Add to cart</div>
  <div class="abs add" style="left:469px">Add to cart</div>
  <div class="abs add" style="left:777px">Add to cart</div>

  <div class="abs arrow" style="left:1002px"><svg width="10" height="14" viewBox="0 0 10 14"><path d="M8 1L2 7l6 6" stroke="#fff" stroke-width="2.5" fill="none"/></svg></div>
  <div class="abs arrow" style="left:1053px"><svg width="10" height="14" viewBox="0 0 10 14"><path d="M2 1l6 6-6 6" stroke="#fff" stroke-width="2.5" fill="none"/></svg></div>
</section>

<footer class="abs footer">
  <div class="abs brand" style="left:127px;top:52px;font-size:21px"><span class="brand-mark"></span>LARKFORGE</div>
  <div class="abs f-line" style="left:96px;top:125px">
    <svg width="14" height="16" viewBox="0 0 14 16" fill="none" stroke="#fff" stroke-width="1.3"><path d="M7 15s5-5 5-9A5 5 0 0 0 2 6c0 4 5 9 5 9z"/><circle cx="7" cy="6" r="1.8"/></svg>
    <span>LarkForge, No.12 Cedar Lane, Boise,<br>Idaho, USA 837 02</span>
  </div>
  <div class="abs f-line" style="left:96px;top:201px">
    <svg width="14" height="14" viewBox="0 0 14 14"><path d="M3 1l2.5 3-1.5 2c1 2 2 3 4 4l2-1.5 3 2.5-1.5 2C6 13 1 8 1 2.5z" fill="#fff"/></svg>
    <span>+1 555 014 2290</span>
  </div>
  <div class="abs f-line" style="left:96px;top:249px">
    <svg width="15" height="12" viewBox="0 0 15 12" fill="none" stroke="#fff" stroke-width="1.2"><rect x="1" y="1" width="13" height="10"/><path d="M1 1l6.5 6L14 1"/></svg>
    <span>hello@larkforge-demo.com</span>
  </div>

  <div class="abs f-head" style="left:531px;top:62px">INFORMATION</div>
  <div class="abs f-link" style="left:532px;top:110px">home</div>
  <div class="abs f-link" style="left:532px;top:142px">about us</div>
  <div class="abs f-link" style="left:532px;top:173px">product</div>
  <div class="abs f-link" style="left:532px;top:204px">manufacture</div>
  <div class="abs f-link" style="left:532px;top:235px">contacts</div>

  <div class="abs f-head" style="left:835px;top:62px">HELP &amp; SUPPORT</div>
  <div class="abs f-link" style="left:835px;top:110px">contacts</div>
  <div class="abs f-link" style="left:835px;top:142px">my account</div>
  <div class="abs f-link" style="left:835px;top:173px">cart</div>
</footer>
<div class="abs copy">© Copyright 2020. All rights reserved.</div>

</body>
</html>
```